Animal Horse & Bedding Company Needs a Website Coded & Designed

We need a website for a new animal bedding and feed company that is visually grabbing and vibrant. We would like to see a website that displays trust, quality and confidence. Needs to be responsive and mobile friendly for all browsers and coded for both Android & IOS. SEO is also important.

Joomla or Wordpress – must be both desktop and mobile friendly with fast page load speed. Need the ability to edit ourselves in Wordpress or Joomla.

Full details attached below with some layout and content ideas.

Coding

Coded - Design and coding required

Number of Pages Required

5+ page

Font styles to use
Sans Serif

Requirements
Must have
• Needs to be responsive and mobile friendly for all browsers and coded for both Android & IOS. SEO is also important.

Wordpress – must be both desktop and mobile friendly with fast page load speed. Need the ability to edit ourselves in Wordpress.

Logo Colours:
Dark Brown
CMYK: 50 / 70 / 80 / 70
Pantone: 4625C

Orange
CMYK: 0 / 50 / 100 / 0
Pantone: 144C
Nice to have
• Use picture of building attached and super impose logo on building.

```html
<!DOCTYPE html>
<html lang="en">
<head>
<meta charset="utf-8">
<title>Golden Bale – Bedding &amp; Feed – Home Page Layouts</title>
<link href="https://fonts.googleapis.com/css2?family=Montserrat:wght@500;600;700&family=Open+Sans:wght@400;600&display=swap" rel="stylesheet">
<style>
:root{
  --orange:#f09c00;
  --brown:#33221a;
  --brown-bar:#3a2618;
  --board:#e8e8e8;
  --ink:#1c1c1c;
  --muted:#8a8a8a;
  --white:#ffffff;
}
*{box-sizing:border-box;margin:0;padding:0}
html,body{width:926px;height:1200px;overflow:hidden;background:var(--board)}
body{font-family:"Open Sans",Arial,sans-serif;color:var(--ink)}
.board{position:absolute;left:0;top:0;width:1685px;height:2184px;transform:scale(0.54955);transform-origin:0 0}
.page{position:absolute;top:79px;width:726px;background:var(--white);overflow:hidden;box-shadow:0 0 6px rgba(0,0,0,.06)}
.page--home-a{left:81px;height:1705px}
.page--home-b{left:879px;height:2025px}
.abs{position:absolute}

/* top bar */
.topbar{position:absolute;left:0;top:0;width:726px;height:29px;background:var(--orange)}
.topbar__contact{position:absolute;left:0;top:0;width:362px;height:29px;background:var(--brown-bar);color:var(--white);font-size:9.5px;display:flex;align-items:center;padding-left:67px;gap:8px}
.topbar__contact svg{width:9px;height:9px}
.topbar__sep{margin:0 8px}
.topbar__social{position:absolute;right:70px;top:10px;display:flex;gap:14px}
.topbar__social span{width:8px;height:8px;border-radius:50%;background:var(--white)}

/* header */
.header{position:absolute;left:0;top:29px;width:726px;height:49px;display:flex;align-items:center}
.brand{position:absolute;left:67px;display:flex;align-items:center;gap:8px}
.brand__dot{width:22px;height:22px;border-radius:50%;background:var(--orange)}
.brand__name{font-family:"Montserrat",sans-serif;font-weight:600;font-size:18px;letter-spacing:2px;color:var(--brown)}
.nav{position:absolute;right:67px;display:flex;gap:14px;font-family:"Montserrat",sans-serif;font-weight:500;font-size:9.5px;color:var(--ink)}
.nav a{color:inherit;text-decoration:none}
.nav .is-active{color:var(--orange)}

/* hero */
.hero{position:absolute;left:0;top:78px;width:726px;height:362px;background:linear-gradient(180deg,#8f6a45 0%,#c98a3f 22%,#7a4d2b 50%,#5b3a1f 75%,#6e5030 100%)}
.hero__title{position:absolute;top:127px;width:100%;text-align:center;font-family:"Montserrat",sans-serif;font-weight:700;font-size:22px;color:var(--white)}
.hero__text{position:absolute;top:160px;width:100%;text-align:center;font-size:10.5px;line-height:17px;font-weight:600;color:var(--white)}
.hero__arrow{position:absolute;top:171px;width:21px;height:20px;background:var(--white);display:flex;align-items:center;justify-content:center}
.hero__arrow svg{width:8px;height:10px}

.btn{position:absolute;height:25px;background:var(--orange);border:2px solid #ffb733;box-shadow:0 0 0 1px var(--orange);color:var(--white);font-family:"Montserrat",sans-serif;font-weight:700;font-size:9px;display:flex;align-items:center;justify-content:center;letter-spacing:.3px}

/* section headings */
.heading{position:absolute;font-family:"Montserrat",sans-serif;font-weight:700;font-size:21px;color:var(--ink)}
.heading--center{left:0;width:726px;text-align:center}
.lede{position:absolute;left:0;width:726px;text-align:center;font-size:8px;line-height:14px;color:var(--muted)}

/* feature cards */
.feature{position:absolute;top:581px;width:190px;height:129px;background:var(--white);box-shadow:0 0 8px rgba(0,0,0,.09);text-align:center}
.feature svg{position:absolute;left:76px;top:14px;width:38px;height:38px}
.feature__title{position:absolute;top:66px;width:100%;font-family:"Montserrat",sans-serif;font-weight:500;font-size:10px}
.feature__text{position:absolute;top:88px;left:8px;right:8px;font-size:8px;line-height:14px;color:var(--muted)}

/* welcome band */
.welcome{position:absolute;left:0;top:766px;width:726px;height:259px;background:linear-gradient(180deg,#a8b0b6 0%,#8b9195 30%,#5e6a4f 55%,#8a3b34 72%,#6a6f5c 100%)}
.welcome__panel{position:absolute;left:67px;top:34px;width:295px;height:190px;background:rgba(255,255,255,.9)}
.welcome__kicker{position:absolute;left:15px;top:16px;font-family:"Montserrat",sans-serif;font-weight:600;font-size:10px}
.welcome__name{position:absolute;left:15px;top:32px;font-family:"Montserrat",sans-serif;font-weight:700;font-size:18px;color:var(--orange)}
.welcome__text{position:absolute;left:15px;top:67px;width:265px;font-size:8.5px;line-height:15px;color:#555;text-align:justify}

/* service cards */
.service{position:absolute;top:1123px;width:283px;height:194px;border-radius:4px;box-shadow:0 0 8px rgba(0,0,0,.12)}
.service--bedding{left:67px;background:linear-gradient(160deg,#c9c2b6 0%,#8c7a66 45%,#5a4a3a 100%)}
.service--feed{left:374px;background:linear-gradient(160deg,#7a4a2a 0%,#b0763f 45%,#c9a86a 100%)}
.service__label{position:absolute;left:20px;top:162px;font-family:"Montserrat",sans-serif;font-weight:500;font-size:11.5px;color:var(--white)}
.service__go{position:absolute;right:16px;top:158px;width:29px;height:29px;border-radius:50%;background:var(--white);display:flex;align-items:center;justify-content:center}

/* bullet */
.bullet{display:inline-block;width:8px;height:8px;border:1.4px solid var(--orange);border-radius:50%;position:relative;margin-right:10px;vertical-align:-1px}
.bullet::after{content:"";position:absolute;left:1.6px;top:2.3px;width:2.2px;height:2.2px;border-top:1.3px solid var(--orange);border-right:1.3px solid var(--orange);transform:rotate(45deg)}

/* benefits */
.benefit-photo{position:absolute;width:260px;height:260px;border-radius:50%;border:4px solid var(--white);box-shadow:0 0 6px rgba(0,0,0,.2)}
.benefit-photo--bedding{background:linear-gradient(150deg,#c9c2b6 0%,#8c7a66 45%,#4f3f30 100%)}
.benefit-photo--feed{background:linear-gradient(150deg,#7a4a2a 0%,#b0763f 45%,#c9a86a 100%)}
.benefit-ring{position:absolute;width:272px;height:272px;border-radius:50%;border:3px solid transparent}
.benefit-ring--left{border-left-color:var(--orange);border-bottom-color:var(--orange);transform:rotate(20deg)}
.benefit-ring--right{border-right-color:var(--orange);border-top-color:var(--orange);transform:rotate(20deg)}
.list{position:absolute;list-style:none;font-size:9.5px;color:#666}
.list li{height:19.7px}
.benefit-text{position:absolute;font-size:8.5px;line-height:13.7px;color:#666}

/* newsletter */
.newsletter{position:absolute;left:67px;width:591px;height:107px;background:var(--white);box-shadow:0 0 10px rgba(0,0,0,.12);z-index:2}
.newsletter__title{position:absolute;left:17px;top:45px;font-family:"Montserrat",sans-serif;font-weight:700;font-size:15.5px}
.field{position:absolute;top:27px;width:138px;height:25px;border:1px solid #ddd;font-size:8.5px;color:#888;padding:7px 7px}
.newsletter .btn{left:288px;top:58px;width:280px;height:23px}

/* footer */
.footer{position:absolute;left:0;width:726px;height:279px;background:var(--brown);color:var(--white)}
.footer__brand{position:absolute;left:0;top:75px;width:726px;display:flex;justify-content:center;align-items:center;gap:9px}
.footer__brand .brand__name{color:var(--white);font-size:21px}
.footer__col{position:absolute;top:130px}
.footer__col h4{font-family:"Open Sans",sans-serif;font-weight:600;font-size:11.5px;margin-bottom:6px}
.footer__col ul{list-style:none;font-size:9px}
.footer__col li{height:14.5px}
.footer__contact li{display:flex;gap:10px;height:auto;line-height:14.5px;margin-bottom:4px}
.footer__contact svg{width:8px;height:9px;margin-top:3px;flex:none}
.footer__rule{position:absolute;left:67px;top:240px;width:591px;height:1px;background:rgba(255,255,255,.2)}
.footer__copy{position:absolute;left:67px;top:252px;font-size:7.5px}
.footer__social{position:absolute;left:558px;top:247px;display:flex;gap:5px}
.footer__social span{width:21px;height:21px;background:var(--white);display:flex;align-items:center;justify-content:center}
.footer__social span::after{content:"";width:7px;height:7px;border-radius:50%;background:var(--orange)}
</style>
</head>
<body>
<div class="board">

<!-- Layout A -->
<section class="page page--home-a">
  <div class="topbar">
    <div class="topbar__contact">
      <svg viewBox="0 0 10 10"><path d="M2 1l2 2-1 1.3c.6 1.2 1.5 2.1 2.7 2.7L7 6l2 2-1.3 1.3C4.5 9 1 5.5.7 2.3z" fill="#fff"/></svg>(555) 010 2030<span class="topbar__sep">|</span>
      <svg viewBox="0 0 10 8"><rect x=".5" y=".5" width="9" height="7" fill="none" stroke="#fff"/><path d="M.5.8L5 4.5 9.5.8" fill="none" stroke="#fff"/></svg>hello@goldenbale.example
    </div>
    <div class="topbar__social"><span></span><span></span><span></span><span></span></div>
  </div>
  <header class="header">
    <div class="brand"><span class="brand__dot"></span><span class="brand__name">GOLDEN BALE</span></div>
    <nav class="nav"><a class="is-active">HOME</a><a>ABOUT</a><a>FEED</a><a>BEDDING</a><a>CONTACT US</a><a>REQUEST QUOTE</a></nav>
  </header>
  <div class="hero" role="img" aria-label="Photo of two cattle standing in tall golden grass at sunset">
    <div class="hero__arrow" style="left:24px"><svg viewBox="0 0 8 10"><path d="M6 1L2 5l4 4" fill="none" stroke="#222" stroke-width="1.4"/></svg></div>
    <div class="hero__arrow" style="right:21px"><svg viewBox="0 0 8 10"><path d="M2 1l4 4-4 4" fill="none" stroke="#222" stroke-width="1.4"/></svg></div>
    <h1 class="hero__title">GOLDEN BALE</h1>
    <p class="hero__text">Looking for the best bedding and feed for your horse, livestock or<br>household pet look no further.</p>
    <span class="btn" style="left:319px;top:206px;width:87px">LEARN MORE</span>
  </div>

  <h2 class="heading heading--center" style="top:490px">WHY CHOOSE US</h2>
  <p class="lede" style="top:525px">The Golden Bale offers supply and delivery of fresh bedding as well as removal of waste bedding.  Let us deliver you a container of<br>fresh straw and haul your waste bedding away.  A full service solution that is sustainable and responsible.</p>

  <div class="feature" style="left:67px">
    <svg viewBox="0 0 38 38" fill="none" stroke="#f09c00" stroke-width="1.5"><circle cx="19" cy="15" r="11"/><circle cx="19" cy="15" r="7"/><path d="M15.5 15l2.5 2.5 4.5-5M12 24l-4 10 5-2 2 4 3-7M26 24l4 10-5-2-2 4-3-7"/></svg>
    <div class="feature__title">QUALITY GUARANTEED</div>
    <p class="feature__text">Grown for quality - 100% natural with no chemicals or additives</p>
  </div>
  <div class="feature" style="left:267px">
    <svg viewBox="0 0 38 38" fill="none" stroke="#f09c00" stroke-width="1.5"><circle cx="19" cy="19" r="16" stroke-dasharray="4 2"/><circle cx="19" cy="19" r="12"/><rect x="10" y="14" width="11" height="8"/><path d="M21 16h4l3 3v3h-7"/><circle cx="13" cy="24" r="1.6"/><circle cx="25" cy="24" r="1.6"/></svg>
    <div class="feature__title">FULL SERVICE SOLUTION</div>
    <p class="feature__text">Dedicated in providing a full service solution of bedding supply &amp; waste removal</p>
  </div>
  <div class="feature" style="left:467px">
    <svg viewBox="0 0 38 38" fill="none" stroke="#f09c00" stroke-width="1.5"><circle cx="22" cy="13" r="7"/><path d="M22 9v8M20 11h3.5a1.3 1.3 0 010 2.5h-3a1.3 1.3 0 000 2.5H24M4 26l7-5h6l8 2-8 1M4 32l7-3h10l11-8"/></svg>
    <div class="feature__title">CONVENIENT&amp; COST EFFECTIVE</div>
    <p class="feature__text">Compressed bags, pellets or bulk products saving in shipping costs</p>
  </div>

  <div class="welcome" role="img" aria-label="Aerial photo of a farm with red barns and paddocks">
    <div class="welcome__panel">
      <div class="welcome__kicker">WELCOME TO</div>
      <div class="welcome__name">GOLDEN BALE</div>
      <p class="welcome__text">Looking for the best bedding and feed for your horse, livestock or household pet look no further.  We use premium locally sourced straw and hay in all of our products and are committed in providing quality products and service.</p>
      <span class="btn" style="left:16px;top:146px;width:86px">LEARN MORE</span>
    </div>
  </div>

  <h2 class="heading heading--center" style="top:1075px">WHAT WE DO</h2>
  <div class="service service--bedding" role="img" aria-label="Photo of a rabbit and a guinea pig on straw bedding">
    <span class="service__label">BEDDING PROVIDES</span>
    <span class="service__go"><span class="bullet" style="margin:0;transform:scale(1.3)"></span></span>
  </div>
  <div class="service service--feed" role="img" aria-label="Photo of horses eating hay">
    <span class="service__label">FEED PROVIDES</span>
    <span class="service__go"><span class="bullet" style="margin:0;transform:scale(1.3)"></span></span>
  </div>

  <div class="newsletter" style="top:1373px">
    <div class="newsletter__title">Subscribe To Our Newsletter</div>
    <div class="field" style="left:288px">Name</div>
    <div class="field" style="left:430px">Email</div>
    <span class="btn">SUBSCRIBE</span>
  </div>
  <footer class="footer" style="top:1426px">
    <div class="footer__brand"><span class="brand__dot"></span><span class="brand__name">GOLDEN BALE</span></div>
    <div class="footer__col" style="left:67px"><h4>Quick Links</h4><ul><li><span class="bullet"></span>Home</li><li><span class="bullet"></span>About</li><li><span class="bullet"></span>Feed</li><li><span class="bullet"></span>Bedding</li><li><span class="bullet"></span>Request Quote</li></ul></div>
    <div class="footer__col" style="left:233px"><h4>About Links</h4><ul><li><span class="bullet"></span>Privacy Policy</li><li><span class="bullet"></span>Terms Of Use</li><li><span class="bullet"></span>Site Map</li></ul></div>
    <div class="footer__col" style="left:398px"><h4>Delivery In</h4><ul><li><span class="bullet"></span>Canada</li><li><span class="bullet"></span>United States</li></ul></div>
    <div class="footer__col footer__contact" style="left:547px"><h4>Contact Us</h4><ul>
      <li><svg viewBox="0 0 8 10"><path d="M4 10S0 5.5 0 3.8a4 4 0 018 0C8 5.5 4 10 4 10z" fill="#f09c00"/></svg>58 Meadow Lane,<br>Fieldtown</li>
      <li><svg viewBox="0 0 10 10"><path d="M2 1l2 2-1 1.3c.6 1.2 1.5 2.1 2.7 2.7L7 6l2 2-1.3 1.3C4.5 9 1 5.5.7 2.3z" fill="#f09c00"/></svg>(555) 010 2030</li>
      <li><svg viewBox="0 0 10 8"><rect width="10" height="8" fill="#f09c00"/></svg>hello@goldenbale.example</li></ul></div>
    <div class="footer__rule"></div>
    <div class="footer__copy">© Copyrights 2021 GOLDEN BALE. All rights reserved</div>
    <div class="footer__social"><span></span><span></span><span></span><span></span></div>
  </footer>
</section>

<!-- Layout B -->
<section class="page page--home-b">
  <div class="topbar">
    <div class="topbar__contact">
      <svg viewBox="0 0 10 10"><path d="M2 1l2 2-1 1.3c.6 1.2 1.5 2.1 2.7 2.7L7 6l2 2-1.3 1.3C4.5 9 1 5.5.7 2.3z" fill="#fff"/></svg>(555) 010 2030<span class="topbar__sep">|</span>
      <svg viewBox="0 0 10 8"><rect x=".5" y=".5" width="9" height="7" fill="none" stroke="#fff"/><path d="M.5.8L5 4.5 9.5.8" fill="none" stroke="#fff"/></svg>hello@goldenbale.example
    </div>
    <div class="topbar__social"><span></span><span></span><span></span><span></span></div>
  </div>
  <header class="header">
    <div class="brand"><span class="brand__dot"></span><span class="brand__name">GOLDEN BALE</span></div>
    <nav class="nav"><a class="is-active">HOME</a><a>ABOUT</a><a>FEED</a><a>BEDDING</a><a>CONTACT US</a><a>REQUEST QUOTE</a></nav>
  </header>
  <div class="hero" role="img" aria-label="Photo of two cattle standing in tall golden grass at sunset">
    <div class="hero__arrow" style="left:24px"><svg viewBox="0 0 8 10"><path d="M6 1L2 5l4 4" fill="none" stroke="#222" stroke-width="1.4"/></svg></div>
    <div class="hero__arrow" style="right:21px"><svg viewBox="0 0 8 10"><path d="M2 1l4 4-4 4" fill="none" stroke="#222" stroke-width="1.4"/></svg></div>
    <h1 class="hero__title">GOLDEN BALE</h1>
    <p class="hero__text">Looking for the best bedding and feed for your horse, livestock or<br>household pet look no further.</p>
    <span class="btn" style="left:319px;top:206px;width:87px">LEARN MORE</span>
  </div>

  <h2 class="heading heading--center" style="top:490px">WHY CHOOSE US</h2>
  <p class="lede" style="top:525px">The Golden Bale offers supply and delivery of fresh bedding as well as removal of waste bedding.  Let us deliver you a container of<br>fresh straw and haul your waste bedding away.  A full service solution that is sustainable and responsible.</p>

  <div class="feature" style="left:67px">
    <svg viewBox="0 0 38 38" fill="none" stroke="#f09c00" stroke-width="1.5"><circle cx="19" cy="15" r="11"/><circle cx="19" cy="15" r="7"/><path d="M15.5 15l2.5 2.5 4.5-5M12 24l-4 10 5-2 2 4 3-7M26 24l4 10-5-2-2 4-3-7"/></svg>
    <div class="feature__title">QUALITY GUARANTEED</div>
    <p class="feature__text">Grown for quality - 100% natural with no chemicals or additives</p>
  </div>
  <div class="feature" style="left:267px">
    <svg viewBox="0 0 38 38" fill="none" stroke="#f09c00" stroke-width="1.5"><circle cx="19" cy="19" r="16" stroke-dasharray="4 2"/><circle cx="19" cy="19" r="12"/><rect x="10" y="14" width="11" height="8"/><path d="M21 16h4l3 3v3h-7"/><circle cx="13" cy="24" r="1.6"/><circle cx="25" cy="24" r="1.6"/></svg>
    <div class="feature__title">FULL SERVICE SOLUTION</div>
    <p class="feature__text">Dedicated in providing a full service solution of bedding supply &amp; waste removal</p>
  </div>
  <div class="feature" style="left:467px">
    <svg viewBox="0 0 38 38" fill="none" stroke="#f09c00" stroke-width="1.5"><circle cx="22" cy="13" r="7"/><path d="M22 9v8M20 11h3.5a1.3 1.3 0 010 2.5h-3a1.3 1.3 0 000 2.5H24M4 26l7-5h6l8 2-8 1M4 32l7-3h10l11-8"/></svg>
    <div class="feature__title">CONVENIENT&amp; COST EFFECTIVE</div>
    <p class="feature__text">Compressed bags, pellets or bulk products saving in shipping costs</p>
  </div>

  <div class="welcome" role="img" aria-label="Aerial photo of a farm with red barns and paddocks">
    <div class="welcome__panel">
      <div class="welcome__kicker">WELCOME TO</div>
      <div class="welcome__name">GOLDEN BALE</div>
      <p class="welcome__text">Looking for the best bedding and feed for your horse, livestock or household pet look no further.  We use premium locally sourced straw and hay in all of our products and are committed in providing quality products and service.</p>
      <span class="btn" style="left:16px;top:146px;width:86px">LEARN MORE</span>
    </div>
  </div>

  <div class="benefit-ring benefit-ring--left" style="left:65px;top:1070px"></div>
  <div class="benefit-photo benefit-photo--bedding" style="left:71px;top:1076px" role="img" aria-label="Round photo of a rabbit and a guinea pig on straw bedding"></div>
  <h2 class="heading" style="left:383px;top:1099px;font-size:19px">BEDDING BENEFITS</h2>
  <ul class="list" style="left:385px;top:1135px">
    <li><span class="bullet"></span>100% Natural Chopped Straw</li>
    <li><span class="bullet"></span>Low Dust</li>
    <li><span class="bullet"></span>Chemical &amp; Additive Free</li>
    <li><span class="bullet"></span>Clean &amp; Highly Absorbent</li>
    <li><span class="bullet"></span>Cheaper than Wood Shavings</li>
    <li><span class="bullet"></span>Economic – less used and less wasted</li>
    <li><span class="bullet"></span>Environmentally Friendly – Recyclable &amp; Compostable</li>
  </ul>
  <span class="btn" style="left:385px;top:1286px;width:87px">VIEW DETAILS</span>

  <h2 class="heading" style="left:67px;top:1394px;font-size:19px">FEED BENEFITS</h2>
  <p class="benefit-text" style="left:67px;top:1428px;width:290px">Hay cubes and pellets are made from premium hay offering a variety of animals a feed that is non-GMO and packed with natural nutrients. These pellets and cubes are less bulky to handle, store and ship.As well, they reduce the amount of wasted feed.</p>
  <ul class="list" style="left:67px;top:1494px">
    <li><span class="bullet"></span>100% Natural</li>
    <li><span class="bullet"></span>Chemical &amp; Additive Free</li>
    <li><span class="bullet"></span>Available in Pellets or Cube</li>
    <li><span class="bullet"></span>High Protein Content</li>
    <li><span class="bullet"></span>Eliminate Waste In Feeding</li>
  </ul>
  <span class="btn" style="left:67px;top:1603px;width:88px">LEARN MORE</span>
  <div class="benefit-ring benefit-ring--right" style="left:388px;top:1378px"></div>
  <div class="benefit-photo benefit-photo--feed" style="left:394px;top:1384px" role="img" aria-label="Round photo of horses eating hay"></div>

  <div class="newsletter" style="top:1694px">
    <div class="newsletter__title">Subscribe To Our Newsletter</div>
    <div class="field" style="left:288px">Name</div>
    <div class="field" style="left:430px">Email</div>
    <span class="btn">SUBSCRIBE</span>
  </div>
  <footer class="footer" style="top:1746px">
    <div class="footer__brand"><span class="brand__dot"></span><span class="brand__name">GOLDEN BALE</span></div>
    <div class="footer__col" style="left:67px"><h4>Quick Links</h4><ul><li><span class="bullet"></span>Home</li><li><span class="bullet"></span>About</li><li><span class="bullet"></span>Feed</li><li><span class="bullet"></span>Bedding</li><li><span class="bullet"></span>Request Quote</li></ul></div>
    <div class="footer__col" style="left:233px"><h4>About Links</h4><ul><li><span class="bullet"></span>Privacy Policy</li><li><span class="bullet"></span>Terms Of Use</li><li><span class="bullet"></span>Site Map</li></ul></div>
    <div class="footer__col" style="left:398px"><h4>Delivery In</h4><ul><li><span class="bullet"></span>Canada</li><li><span class="bullet"></span>United States</li></ul></div>
    <div class="footer__col footer__contact" style="left:547px"><h4>Contact Us</h4><ul>
      <li><svg viewBox="0 0 8 10"><path d="M4 10S0 5.5 0 3.8a4 4 0 018 0C8 5.5 4 10 4 10z" fill="#f09c00"/></svg>58 Meadow Lane,<br>Fieldtown</li>
      <li><svg viewBox="0 0 10 10"><path d="M2 1l2 2-1 1.3c.6 1.2 1.5 2.1 2.7 2.7L7 6l2 2-1.3 1.3C4.5 9 1 5.5.7 2.3z" fill="#f09c00"/></svg>(555) 010 2030</li>
      <li><svg viewBox="0 0 10 8"><rect width="10" height="8" fill="#f09c00"/></svg>hello@goldenbale.example</li></ul></div>
    <div class="footer__rule"></div>
    <div class="footer__copy">© Copyrights 2021 GOLDEN BALE. All rights reserved</div>
    <div class="footer__social"><span></span><span></span><span></span><span></span></div>
  </footer>
</section>

</div>
</body>
</html>
```